Austin TX First Veterinary Urgent Care

We need a flyer designed for us and our clinic that is eye-catching but also summarizes the advantages of our services. We want to express that we are family owned, have convenient hours and affordable prices. We are the first veterinary urgent care animal clinic in Austin Texas. Our hours of operation are M-F 12PM-9PM S-S 10AM-6PM. Our Address is 4871 W Larkspur Rd Suite B212 Austin, Tx 78753. Our phone number is (737)555-0148 our website is www.brookpawclinic.com and our email address is info@brookpawclinic.com.

Target Market(s)

Pet owners and veterinary professionals for referral purposes.

Industry/Entity Type

Veterinary

Font styles to use
Sans Serif

Colors
0094D4
00A9DD
6FCCEA
C7EBF8
E9F6FB
00AB8E
00BBA5
67D7C9
C6EFE9
E9F9F6

Requirements
Must have
• Our logo, hours of operation and contact information easy to read. Should emphasize that we are affordable as well as family owned. List of services should also be displayed: ear, eye, and skin issues, limping, broken toenails, lacerations, coughing, sneezing, allergies, vomiting and diarrhea, urinary issues, constipation, snake bites, toxin ingestion, and many many more
Nice to have
• We would like to have a modern feel with drawn/cartoon images, not realistic stock photos of dogs/cats.

```html
<!DOCTYPE html>
<html lang="en">
<head>
<meta charset="utf-8">
<title>BrookPaw Veterinary Urgent Care Flyer</title>
<link href="https://fonts.googleapis.com/css2?family=Poppins:wght@400;500;600;700;800&family=Bebas+Neue&display=swap" rel="stylesheet">
<style>
:root{
  --navy:#10108a;
  --green:#45ac55;
  --green-bright:#4fbe5c;
  --white:#ffffff;
  --ink:#1a1a2e;
  --illustration-top:#3a38b0;
  --illustration-warm:#f0a060;
}
*{margin:0;padding:0;box-sizing:border-box}
html,body{width:865px;height:1200px;overflow:hidden;background:#fff}
body{font-family:'Poppins',sans-serif;color:var(--ink)}
.flyer{position:relative;width:865px;height:1200px;overflow:hidden;background:var(--white)}
.backdrop{position:absolute;inset:0}
.abs{position:absolute}

.hero-art{left:448px;top:96px;width:417px;height:380px;border-radius:50% 0 0 30%;
  background:linear-gradient(160deg,var(--illustration-top),#5a5ad0 55%,var(--illustration-warm));opacity:.85}

.brand{left:58px;top:62px;display:flex;align-items:center;gap:14px}
.brand-dot{width:58px;height:58px;border-radius:50%;background:var(--green)}
.brand-name{font-weight:800;font-size:44px;line-height:1;color:var(--white);letter-spacing:-1px}
.brand-tag{left:130px;top:118px;font-size:12px;font-weight:500;color:var(--white);letter-spacing:.5px}

.kicker{left:60px;top:170px;font-size:26px;font-weight:600;color:var(--white);letter-spacing:10px;white-space:nowrap}
.headline{left:57px;top:206px;font-weight:800;line-height:.92;font-size:59px;letter-spacing:-.5px}
.headline .green{color:var(--green-bright)}
.headline .white{color:var(--white)}

.badge{left:510px;top:352px;width:214px;height:214px;border-radius:50%;background:var(--navy);
  outline:6px solid var(--navy);outline-offset:2px;border:3px solid var(--white);
  display:flex;flex-direction:column;align-items:center;justify-content:center;color:var(--white)}
.badge-top{font-weight:700;font-size:22px;letter-spacing:.5px}
.badge-main{font-family:'Bebas Neue',sans-serif;font-size:72px;line-height:.9;color:var(--green-bright)}

.services-title{left:53px;top:528px;font-size:40px;line-height:1.2;color:var(--navy);font-weight:800}
.services-title span{color:var(--green);font-weight:400}
.service-col{list-style:none;font-size:22px;font-weight:500;color:var(--ink);line-height:1.05}
.service-col li{position:relative;padding-left:24px;margin-bottom:17px;white-space:nowrap}
.service-col li::before{content:"";position:absolute;left:0;top:5px;width:16px;height:16px;border:2px solid var(--navy);border-radius:2px}
.service-col li::after{content:"";position:absolute;left:5px;top:7px;width:5px;height:9px;border:solid var(--green);border-width:0 2px 2px 0;transform:rotate(40deg)}

.pet-art{left:440px;top:775px;width:385px;height:200px;border-radius:45% 45% 35% 35%;
  background:linear-gradient(120deg,#f3a462,#e07a3a 60%,#7a4a30);opacity:.8}

.pill{left:51px;width:368px;height:46px;border-radius:8px;display:flex;align-items:center;justify-content:center;
  font-weight:700;font-size:21px;color:var(--white);box-shadow:0 6px 8px rgba(0,0,0,.25)}
.pill-green{top:794px;background:var(--green)}
.pill-navy{top:852px;background:var(--navy)}

.cta{left:56px;top:934px;font-size:20px;font-weight:700;color:var(--green)}
.cta b{color:var(--navy)}
.phone{left:56px;top:966px;display:flex;align-items:center;gap:4px;font-size:43px;font-weight:800;color:var(--navy);letter-spacing:.5px}
.contact{left:58px;font-size:17px;font-weight:500;color:var(--ink);display:flex;gap:6px;align-items:flex-start;line-height:1.05}
.contact-mail{top:1038px}
.contact-pin{top:1070px}
.web{left:58px;top:1122px;font-size:22px;letter-spacing:1px;color:var(--ink);white-space:nowrap}
.web b{color:var(--navy);font-weight:700}

.hours-title{left:524px;top:1038px;font-size:21px;font-weight:700;color:var(--white)}
.hours-row{left:520px;display:flex;align-items:center;gap:10px;font-size:30px;font-weight:700;color:var(--white)}
.hours-row .days{color:var(--navy);font-weight:500;width:72px;border-right:2px solid var(--white);padding-right:6px;line-height:1.1}
.hours-row .time{color:var(--navy)}
.hours-mf{top:1072px}
.hours-ss{top:1114px}
.clock{width:24px;height:24px}
</style>
</head>
<body>
<main class="flyer">
  <svg class="backdrop" width="865" height="1200" viewBox="0 0 865 1200" aria-hidden="true">
    <path d="M0 0H865V575C820 540 760 500 700 470C620 440 560 470 470 500C380 530 300 500 200 480C120 465 50 470 0 490Z" fill="var(--navy)"/>
    <path d="M0 490C60 460 140 455 220 470C310 490 380 520 460 495C560 462 620 440 700 470C760 495 820 535 865 570V590C820 560 760 520 700 495C620 465 560 490 470 515C380 545 300 520 210 500C120 482 50 490 0 505Z" fill="var(--green)"/>
    <path d="M320 1200C420 1140 470 1060 560 1010C680 945 780 965 865 905V1200Z" fill="var(--navy)"/>
    <path d="M335 1200C430 1140 480 1070 570 1022C690 960 790 982 865 925V1200Z" fill="var(--green)"/>
  </svg>

  <div class="abs hero-art" role="img" aria-label="Cartoon illustration of a smiling young man hugging a cat and a dog, with a syringe and medicine bottle"></div>

  <div class="abs brand"><span class="brand-dot"></span><span class="brand-name">BrookPaw</span></div>
  <div class="abs brand-tag">VETERINARY URGENT CARE</div>

  <div class="abs kicker">AUSTIN TX FIRST</div>
  <h1 class="abs headline"><span class="green">VETERINARY</span><br><span class="white">URGENT<br>CARE</span></h1>

  <div class="abs badge"><span class="badge-top">AFFORDABLE</span><span class="badge-main">PRICES</span></div>

  <h2 class="abs services-title"><span>OUR</span> SERVICES</h2>
  <ul class="abs service-col" style="left:58px;top:604px"><li>Ear</li><li>Eye</li><li>Skin issues</li><li>Limping</li></ul>
  <ul class="abs service-col" style="left:225px;top:604px"><li>Broken toenails</li><li>Lacerations</li><li>Coughing</li><li>Sneezing</li></ul>
  <ul class="abs service-col" style="left:447px;top:604px"><li>Allergies</li><li>Vomiting &amp;<br>Diarrhea</li><li>Urinary</li></ul>
  <ul class="abs service-col" style="left:618px;top:604px"><li>Issues</li><li>Constipation</li><li>Snake bites</li><li>Toxin ingestion</li></ul>

  <div class="abs pet-art" role="img" aria-label="Cartoon illustration of a playful orange cat and a corgi-style dog"></div>

  <div class="abs pill pill-green">WE HAVE CONVENIENT HOURS</div>
  <div class="abs pill pill-navy">WE ARE FAMILY OWNED</div>

  <p class="abs cta">Call us to make <b>AN APPOINTMENT</b></p>
  <p class="abs phone">
    <svg width="34" height="34" viewBox="0 0 24 24" aria-hidden="true"><path d="M6.6 10.8a15.1 15.1 0 0 0 6.6 6.6l2.2-2.2a1 1 0 0 1 1-.25 11.4 11.4 0 0 0 3.6.57 1 1 0 0 1 1 1V20a1 1 0 0 1-1 1A17 17 0 0 1 3 4a1 1 0 0 1 1-1h3.5a1 1 0 0 1 1 1c0 1.25.2 2.450.57 3.6a1 1 0 0 1-.25 1Z" fill="var(--green)"/></svg>
    (737)555-0148
  </p>
  <p class="abs contact contact-mail">
    <svg width="18" height="14" viewBox="0 0 18 14" aria-hidden="true"><rect width="18" height="14" rx="1" fill="var(--green)"/><path d="M1 1l8 6 8-6" stroke="#fff" stroke-width="1.5" fill="none"/></svg>
    info@brookpawclinic.com
  </p>
  <p class="abs contact contact-pin">
    <svg width="16" height="22" viewBox="0 0 16 22" aria-hidden="true"><path d="M8 0a8 8 0 0 0-8 8c0 6 8 14 8 14s8-8 8-14a8 8 0 0 0-8-8Z" fill="var(--green)"/><circle cx="8" cy="8" r="3" fill="#fff"/></svg>
    <span>4871 W Larkspur Rd Suite B212 Austin<br>Tx 78753</span>
  </p>
  <p class="abs web">www.<b>brookpawclinic</b>.com</p>

  <p class="abs hours-title">Our hours of operation are</p>
  <div class="abs hours-row hours-mf">
    <svg class="clock" viewBox="0 0 24 24" aria-hidden="true"><circle cx="12" cy="12" r="10" fill="none" stroke="#fff" stroke-width="2.5"/><path d="M12 7v5l3 2" stroke="#fff" stroke-width="2" fill="none"/></svg>
    <span class="days">M-F</span><span class="time">12PM-9PM</span>
  </div>
  <div class="abs hours-row hours-ss">
    <svg class="clock" viewBox="0 0 24 24" aria-hidden="true"><circle cx="12" cy="12" r="10" fill="none" stroke="#fff" stroke-width="2.5"/><path d="M12 7v5l3 2" stroke="#fff" stroke-width="2" fill="none"/></svg>
    <span class="days">S-S</span><span class="time">10AM-6PM</span>
  </div>
</main>
</body>
</html>
```